Business Card Design

Business sales of reconditioned / used batteries with mobile delivery and install services. Customers base majority are auto car sales lots and individuals.

Card need to convey quality product reliability and quick prompt professional service.

Card must reflect excellence in customer care and product being offered

Target Market(s)

Auto car lots new and used. Auto repair shops. Individuals.

Industry/Entity Type

Business

Contact Information for Business Card

Batteries Q-Swift
Cars, Trucks, Boats, Motorcycles, lawn mowers, power tools
Delivery & install available most vehicles
Mon-Sat 9-6pm
Dale Morrick 501-738-2054
*product warranty 6 month shelf life battery/1 year blems battery

```html
<!DOCTYPE html>
<html lang="en">
<head>
<meta charset="utf-8">
<title>Batteries Q-Swift – Business Card</title>
<link rel="stylesheet" href="https://fonts.googleapis.com/css2?family=Source+Sans+3:wght@400;600;700&display=swap">
<style>
  :root {
    --page: #ffffff;
    --card-white: #ffffff;
    --card-black: #000000;
    --ink: #111111;
    --red: #e30613;
    --red-soft: #f4a58a;
    --text-light: #ffffff;
    --font: "Source Sans 3", "Myriad Pro", Arial, sans-serif;
  }
  * { box-sizing: border-box; margin: 0; padding: 0; }
  html, body {
    width: 1200px; height: 1000px; overflow: hidden;
    background: var(--page);
    font-family: var(--font);
  }
  .card {
    position: absolute; left: 57px; top: 166px;
    width: 1086px; height: 637px;
    background: var(--card-black);
    box-shadow: 4px 6px 12px rgba(0,0,0,0.25);
    overflow: hidden;
  }
  .card__header {
    position: absolute; left: 0; top: 0; width: 100%; height: 196px;
    background: var(--card-white);
  }
  .brand {
    position: absolute; left: 0; right: 0; top: 72px;
    display: flex; justify-content: center; align-items: center; gap: 18px;
    color: var(--ink);
    font-weight: 700;
  }
  .brand__mark {
    width: 26px; height: 26px; background: var(--red);
  }
  .brand__name {
    font-size: 70px; line-height: 1; letter-spacing: 0.5px;
    text-transform: uppercase;
  }
  .brand__suffix {
    position: absolute; right: 212px; top: 148px;
    font-size: 34px; font-weight: 700; color: var(--ink); line-height: 1;
  }
  .accent-bar {
    position: absolute; left: 0; top: 196px; width: 100%; height: 24px;
    background: linear-gradient(90deg, var(--card-white) 12%, var(--red-soft) 45%, var(--red) 85%);
  }
  .services {
    position: absolute; left: 62px; top: 235px;
    list-style: none; color: var(--text-light);
    font-size: 31px; line-height: 39.7px;
  }
  .services__item { display: flex; align-items: center; gap: 10px; }
  .services__icon { width: 26px; height: 22px; flex: none; }
  .warranty {
    position: absolute; left: 58px; top: 560px;
    color: var(--text-light); font-size: 25px; line-height: 1;
  }
  .contact {
    position: absolute; right: 60px; top: 298px;
    text-align: right; color: var(--text-light);
  }
  .contact__name { font-size: 42px; font-weight: 400; line-height: 1; letter-spacing: 0.5px; text-transform: uppercase; }
  .contact__phone { font-size: 56px; font-weight: 700; line-height: 1; margin-top: 8px; }
  .contact__hours { font-size: 35px; line-height: 1; margin-top: 44px; }
</style>
</head>
<body>
  <article class="card">
    <header class="card__header">
      <div class="brand">
        <span class="brand__mark"></span>
        <span class="brand__name">Batteries Q-Swift</span>
      </div>
      <span class="brand__suffix">LLC</span>
    </header>
    <div class="accent-bar"></div>

    <ul class="services">
      <li class="services__item"><svg class="services__icon" viewBox="0 0 26 22"><path d="M0 0h7l7 11-7 11H0l7-11z M11 0h7l7 11-7 11h-7l7-11z" fill="#e30613"/></svg>Cars</li>
      <li class="services__item"><svg class="services__icon" viewBox="0 0 26 22"><path d="M0 0h7l7 11-7 11H0l7-11z M11 0h7l7 11-7 11h-7l7-11z" fill="#e30613"/></svg>Trucks</li>
      <li class="services__item"><svg class="services__icon" viewBox="0 0 26 22"><path d="M0 0h7l7 11-7 11H0l7-11z M11 0h7l7 11-7 11h-7l7-11z" fill="#e30613"/></svg>Boats</li>
      <li class="services__item"><svg class="services__icon" viewBox="0 0 26 22"><path d="M0 0h7l7 11-7 11H0l7-11z M11 0h7l7 11-7 11h-7l7-11z" fill="#e30613"/></svg>Motorcycles</li>
      <li class="services__item"><svg class="services__icon" viewBox="0 0 26 22"><path d="M0 0h7l7 11-7 11H0l7-11z M11 0h7l7 11-7 11h-7l7-11z" fill="#e30613"/></svg>Lawn mowers</li>
      <li class="services__item"><svg class="services__icon" viewBox="0 0 26 22"><path d="M0 0h7l7 11-7 11H0l7-11z M11 0h7l7 11-7 11h-7l7-11z" fill="#e30613"/></svg>Power tools</li>
      <li class="services__item"><svg class="services__icon" viewBox="0 0 26 22"><path d="M0 0h7l7 11-7 11H0l7-11z M11 0h7l7 11-7 11h-7l7-11z" fill="#e30613"/></svg>Delivery &amp; Install available</li>
      <li class="services__item"><svg class="services__icon" viewBox="0 0 26 22"><path d="M0 0h7l7 11-7 11H0l7-11z M11 0h7l7 11-7 11h-7l7-11z" fill="#e30613"/></svg>Most vehicles</li>
    </ul>

    <p class="warranty">*product warranty 6 month shelf life battery/1 year blems battery</p>

    <div class="contact">
      <p class="contact__name">Dale Morrick</p>
      <p class="contact__phone">501-738-2054</p>
      <p class="contact__hours">Monday-Saturday 9-6pm</p>
    </div>
  </article>
</body>
</html>
```